Campaign Website

I need a website for my judicial campaign. I would like a site that directs from this domain as well as a new domain with my married last name. I need separate pages on the site that address my diversion programs, and a page to allow people to donate with a link to my bank account and a link for people to submit requests to volunteer, get yard signs, etc.

```html
<!DOCTYPE html>
<html lang="en">
<head>
<meta charset="utf-8">
<title>Judge Renata Holloway Campaign</title>
<link rel="stylesheet" href="https://fonts.googleapis.com/css2?family=Lato:wght@400;700;900&display=swap">
<style>
:root{
  --navy:#1f2a84;
  --blue:#253391;
  --red:#e4072d;
  --magenta:#8c1350;
  --grey:#f1f1f1;
  --ink:#222;
  --text:#333;
  --footer:#262626;
}
*{box-sizing:border-box;margin:0;padding:0}
html,body{width:1200px;height:3370px;overflow:hidden}
body{font-family:'Lato',sans-serif;color:var(--text);background:#fff;position:relative}
.abs{position:absolute}
.btn{display:inline-block;background:var(--red);color:#fff;font-weight:700;font-size:14px;text-transform:uppercase;text-decoration:none;padding:0;width:152px;height:48px;line-height:48px;text-align:center}
/* header */
.site-header{position:absolute;left:0;top:0;width:1200px;height:135px;background:#fff}
.brand{left:75px;top:44px;font-weight:900;font-size:34px;color:#111;letter-spacing:-0.5px}
.donate-top{left:1008px;top:21px;width:118px;height:46px;line-height:46px;text-transform:none;font-size:17px;font-weight:400}
.main-nav{right:74px;top:86px;display:flex;gap:33px;font-size:17px;font-weight:700}
.main-nav a{color:#222;text-decoration:none}
.main-nav a.active{color:var(--navy)}
/* hero */
.hero{left:0;top:135px;width:1200px;height:528px;background:linear-gradient(90deg,#3c2a22 0%,#5a4032 45%,#6b4c3a 70%,#4a3429 100%)}
.hero h1{position:absolute;left:75px;top:144px;color:#fff;font-weight:900;font-size:47px;line-height:51px;text-transform:uppercase}
.hero .btn{position:absolute;left:75px;top:328px;font-size:15px}
.dots{position:absolute;left:560px;top:468px;display:flex;gap:11px}
.dots i{width:12px;height:12px;border-radius:50%;background:#fff;display:block}
.dots i:first-child{background:#111;border:2px solid #fff}
/* welcome */
.welcome{left:0;top:663px;width:1200px;height:394px;text-align:center}
.welcome h2{margin-top:52px;color:var(--navy);font-weight:900;font-size:38px}
.welcome .quote{color:var(--red);font-size:17px;line-height:27px;width:900px;margin:18px auto 0}
.welcome .body{font-size:14.5px;line-height:27px;width:1020px;margin:14px auto 0;color:#333}
.welcome .btn{margin-top:36px}
/* bio */
.bio-bg{left:0;top:1057px}
.bio-text{left:75px;top:1185px;width:495px;color:#fff}
.bio-text h2{font-size:38px;font-weight:900;text-transform:uppercase}
.bio-text p{margin-top:18px;font-size:14.5px;line-height:28px}
.bio-text .btn{margin-top:34px}
.bio-photo{left:588px;top:1148px;width:538px;height:542px;background:linear-gradient(160deg,#5b5f6e 0%,#3a3c44 45%,#121214 100%)}
/* cards */
.card{top:1773px;width:330px;height:334px;background:var(--navy);border:4px solid #c9c9cf;color:#fff;text-align:center;padding-top:40px}
.card svg{display:block;margin:0 auto}
.card h3{margin-top:16px;font-size:24px;font-weight:900;text-transform:uppercase}
.card p{margin:14px auto 0;width:285px;font-size:14px;line-height:24px}
.card .btn{margin-top:24px}
/* diversion */
.div-photo{left:75px;top:2189px;width:539px;height:543px;background:linear-gradient(135deg,#2b2b2b 0%,#1b1b1b 50%,#3a3630 100%)}
.div-text{left:630px;top:2220px;width:496px;text-align:right}
.div-text h2{color:var(--navy);font-weight:900;font-size:38px;line-height:40px;text-transform:uppercase}
.div-text p{margin-top:26px;font-size:14.5px;line-height:27.5px}
.div-text .btn{margin-top:34px}
/* contact */
.contact{left:75px;top:2833px;width:1051px;height:282px;background:var(--grey);text-align:center}
.contact h2{margin-top:38px;color:var(--navy);font-weight:900;font-size:38px;text-transform:uppercase}
.contact .row{margin-top:14px;font-size:17px;color:#222;display:flex;justify-content:center;gap:34px;align-items:center}
.contact .row span{display:inline-flex;align-items:center;gap:10px}
.contact .btn{margin-top:20px}
/* footer */
.site-footer{left:0;top:3171px;width:1200px;height:199px;background:var(--footer);text-align:center;color:#ddd}
.foot-nav{margin-top:60px;display:flex;justify-content:center;gap:33px;font-size:17px}
.foot-nav a{color:#ddd;text-decoration:none}
.copy{margin-top:18px;font-size:12.5px;color:#8a8a8a}
.social{margin-top:16px;display:flex;justify-content:center;gap:20px}
.social i{width:20px;height:20px;border-radius:50%;background:#ddd;display:block}
</style>
</head>
<body>

<header class="site-header">
  <div class="abs brand">HOLLOWAY RENATA</div>
  <a class="abs btn donate-top" href="#donate">Donate</a>
  <nav class="abs main-nav">
    <a class="active" href="#home">Home</a>
    <a href="#biography">Biography</a>
    <a href="#events">Events</a>
    <a href="#endorsements">Endorsements</a>
    <a href="#voting">Voting Information</a>
    <a href="#contact">Contact</a>
  </nav>
</header>

<section class="abs hero" role="img" aria-label="Photo of the candidate and her husband embracing in front of a dark wooden fence">
  <h1>Judge<br>Renata Holloway<br>Campaign</h1>
  <a class="btn" href="#enter">Enter Now</a>
  <div class="dots"><i></i><i></i><i></i><i></i></div>
</section>

<section class="abs welcome">
  <h2>WELCOME TO MY WEBSITE</h2>
  <p class="quote">“Thank you Brookfield County for your support and votes! Because of you, I am proud to say that I am the Democratic Judge of the 418th Judicial District Court.</p>
  <p class="body">My candidacy is based on the belief that the judiciary needs to be accountable to the citizens it serves. This starts with being present and accessible to ensure that both victims of crime, as well as those accused, have their day in court without unnecessary delays.&nbsp; Additionally, it is incumbent upon the judiciary to be proactive and innovative by starting programs that work to deter crime and reduce the recidivism rate.</p>
  <a class="btn" href="#read">Read More</a>
</section>

<svg class="abs bio-bg" width="1200" height="1116" viewBox="0 0 1200 1116" aria-hidden="true">
  <defs>
    <linearGradient id="bioGrad" x1="0" y1="0" x2="0" y2="1">
      <stop offset="0" stop-color="#7d1452"/>
      <stop offset="1" stop-color="#243290"/>
    </linearGradient>
  </defs>
  <rect x="0" y="586" width="1200" height="530" fill="#f1f1f1"/>
  <polygon points="1200,243 1200,586 0,586 0,458" fill="#fff"/>
  <polygon points="0,0 1200,0 1200,243 314,586 0,458" fill="url(#bioGrad)"/>
</svg>

<div class="abs bio-text" id="biography">
  <h2>Biography</h2>
  <p>I was born in Cedar Falls, Ohio, the middle child of five siblings to Curtis and Lorraine Holloway. I matriculated at Northbridge State University where I received a Bachelor of Arts in Political Science. I earned my Juris Doctorate from the Westmoor School of Law where I served as the President of the Black Law Students Association.</p>
  <a class="btn" href="#bio">Read More</a>
</div>
<div class="abs bio-photo" role="img" aria-label="Portrait of the candidate in judicial robe in front of flags"></div>

<div class="abs card" style="left:75px" id="events">
  <svg width="52" height="56" viewBox="0 0 52 56" aria-hidden="true"><rect x="2" y="8" width="48" height="46" rx="3" fill="#fff"/><rect x="10" y="2" width="6" height="12" rx="2" fill="#fff"/><rect x="36" y="2" width="6" height="12" rx="2" fill="#fff"/><g fill="#1f2a84"><rect x="7" y="20" width="8" height="7"/><rect x="17" y="20" width="8" height="7"/><rect x="27" y="20" width="8" height="7"/><rect x="37" y="20" width="8" height="7"/><rect x="7" y="30" width="8" height="7"/><rect x="17" y="30" width="8" height="7"/><rect x="27" y="30" width="8" height="7"/><rect x="37" y="30" width="8" height="7"/><rect x="7" y="40" width="8" height="7"/><rect x="17" y="40" width="8" height="7"/><rect x="27" y="40" width="8" height="7"/><rect x="37" y="40" width="8" height="7"/></g></svg>
  <h3>Events</h3>
  <p>Cras convallis ligula ut lorem vehicula, vel lacinia lacus volutpat. Nullam tempus ut leo non accumsan.</p>
  <a class="btn" href="#events">Read More</a>
</div>
<div class="abs card" style="left:436px" id="endorsements">
  <svg width="46" height="56" viewBox="0 0 46 56" aria-hidden="true"><path d="M2 2h28l14 14v38H2z" fill="#fff"/><path d="M30 2v14h14" fill="#c9c9cf"/><g fill="#1f2a84"><rect x="10" y="26" width="26" height="3"/><rect x="10" y="33" width="26" height="3"/><rect x="10" y="40" width="26" height="3"/></g></svg>
  <h3>Endorsements</h3>
  <p>Cras convallis ligula ut lorem vehicula, vel lacinia lacus volutpat. Nullam tempus ut leo non accumsan.</p>
  <a class="btn" href="#endorsements">Read More</a>
</div>
<div class="abs card" style="left:797px" id="voting">
  <svg width="60" height="56" viewBox="0 0 60 56" aria-hidden="true"><path d="M16 10l10-8 10 12" stroke="#fff" stroke-width="4" fill="none"/><rect x="2" y="20" width="56" height="34" fill="#fff"/><text x="30" y="45" text-anchor="middle" font-family="Lato,sans-serif" font-weight="900" font-size="17" fill="#1f2a84">VOTE</text></svg>
  <h3>Voting Information</h3>
  <p>Cras convallis ligula ut lorem vehicula, vel lacinia lacus volutpat. Nullam tempus ut leo non accumsan.</p>
  <a class="btn" href="#voting">Read More</a>
</div>

<svg class="abs" style="left:0;top:2577px" width="1200" height="594" viewBox="0 0 1200 594" aria-hidden="true">
  <defs>
    <linearGradient id="footGrad" x1="0" y1="0" x2="0" y2="1">
      <stop offset="0" stop-color="#243290"/>
      <stop offset="1" stop-color="#a8104e"/>
    </linearGradient>
  </defs>
  <polygon points="1200,0 1200,594 0,594 0,492" fill="url(#footGrad)"/>
</svg>

<div class="abs div-photo" role="img" aria-label="Photo of small wooden figures beside a wooden courthouse model"></div>
<div class="abs div-text">
  <h2>My Diversion<br>Programs</h2>
  <p>Cras convallis ligula ut lorem vehicula, vel lacinia lacus volutpat. Nullam tempus ut leo non accumsan. Cras lectus odio, tempor eget dolor eget, molestie porta dui Fusce fermentum ultricies enim vel interdum. Proin eros purus, pellentesque id risus sit amet, auctor auctor velit.</p>
  <a class="btn" href="#diversion">Read More</a>
</div>

<section class="abs contact" id="contact">
  <h2>Get In Touch With Me</h2>
  <div class="row"><span><svg width="11" height="15" viewBox="0 0 11 15" aria-hidden="true"><path d="M5.5 0A5.5 5.5 0 0 0 0 5.5C0 9.5 5.5 15 5.5 15S11 9.5 11 5.5A5.5 5.5 0 0 0 5.5 0zm0 8A2.5 2.5 0 1 1 5.5 3a2.5 2.5 0 0 1 0 5z" fill="#222"/></svg>PO Box 40218 Brookfield, Ohio 44012</span></div>
  <div class="row">
    <span><svg width="15" height="15" viewBox="0 0 15 15" aria-hidden="true"><path d="M3 0l3 4-2 2c1 2 3 4 5 5l2-2 4 3-2 3C6 15 0 9 0 3z" fill="#222"/></svg>(555) 014-2837</span>
    <span><svg width="17" height="13" viewBox="0 0 17 13" aria-hidden="true"><rect width="17" height="13" rx="1" fill="#222"/><path d="M1 1l7.5 6L16 1" stroke="#f1f1f1" stroke-width="1.5" fill="none"/></svg>renataforjudge418@example.com</span>
  </div>
  <a class="btn" href="#contact">Contact Us</a>
</section>

<footer class="abs site-footer">
  <nav class="foot-nav">
    <a href="#home">Home</a><a href="#biography">Biography</a><a href="#events">Events</a><a href="#endorsements">Endorsements</a><a href="#voting">Voting Information</a><a href="#contact">Contact</a><a href="#donate">Donate</a>
  </nav>
  <p class="copy">Copyright © 2019 Company Name All Right Reserved</p>
  <div class="social" aria-label="Social links"><i></i><i></i><i></i><i></i><i></i></div>
</footer>

</body>
</html>
```